holloway paving service

Needs to have phone number 0418259730 and email markholloway@brightmail.com.au.
ABN 62318470915
name mark holloway

For all your concreting solutions
Excavation
Exposed & colour concrete
House & shed slabs
Driveways
Landing & steps

Contact Information for Business Card

ph 0418259730
email markholloway@brightmail.com.au.
ABN 62318470915
name mark holloway

```html
<!DOCTYPE html>
<html lang="en">
<head>
<meta charset="utf-8">
<title>Holloway Paving Service – Business Card</title>
<link rel="stylesheet" href="https://fonts.googleapis.com/css2?family=Barlow:wght@400;500&family=Barlow+Condensed:wght@500;600&display=swap">
<style>
  :root {
    --orange: #ef6a24;
    --orange-light: #f4884d;
    --charcoal: #5f5f62;
    --charcoal-dark: #505053;
    --paper: #ffffff;
    --stripe: #f1f1f1;
    --text-grey: #57575a;
    --backdrop: #e7e4df;
  }
  * { box-sizing: border-box; margin: 0; padding: 0; }
  html, body { width: 1200px; height: 950px; overflow: hidden; }
  body {
    background: var(--backdrop);
    font-family: "Barlow", Arial, sans-serif;
    display: flex;
    flex-direction: column;
    align-items: center;
    justify-content: center;
    gap: 46px;
  }
  .card {
    position: relative;
    width: 720px;
    height: 412px;
    overflow: hidden;
    box-shadow: 0 6px 18px rgba(0,0,0,.18);
  }
  /* ---------- front ---------- */
  .card-front { background: var(--charcoal); }
  .card-front .panels { position: absolute; inset: 0; }
  .company-block {
    position: absolute;
    top: 46px; left: 40px;
    width: 300px;
    color: var(--paper);
    text-align: center;
  }
  .company-name {
    font-family: "Barlow Condensed", Arial Narrow, sans-serif;
    font-weight: 600;
    font-size: 34px;
    letter-spacing: .5px;
    line-height: 1;
  }
  .company-sub {
    display: flex; align-items: center; justify-content: center; gap: 12px;
    font-size: 21px; letter-spacing: 2px; line-height: 1.2; margin-top: 4px;
  }
  .company-sub::before, .company-sub::after {
    content: ""; width: 56px; height: 2px; background: currentColor;
  }
  .company-phone { font-size: 21px; letter-spacing: 1.5px; line-height: 1.1; }
  .brand-feature {
    position: absolute;
    left: 44px; top: 232px;
    display: flex; align-items: center; gap: 14px;
    color: var(--paper);
    font-family: "Barlow Condensed", Arial Narrow, sans-serif;
    font-weight: 600; font-size: 30px; letter-spacing: 1px;
  }
  .brand-feature .mark-square { width: 24px; height: 24px; background: var(--paper); }
  .contact-block {
    position: absolute;
    top: 92px; right: 46px;
    text-align: right;
    color: var(--paper);
  }
  .person-name {
    font-family: "Barlow Condensed", Arial Narrow, sans-serif;
    font-weight: 600; font-size: 36px; letter-spacing: .5px;
    margin-bottom: 14px;
  }
  .contact-line { font-size: 18px; line-height: 1.55; letter-spacing: .5px; }
  .abn {
    position: absolute;
    left: 310px; bottom: 34px;
    color: var(--paper);
    font-size: 17px; letter-spacing: 1px;
  }
  /* ---------- back ---------- */
  .card-back { background: var(--paper); }
  .services {
    position: absolute;
    top: 58px; left: 46px;
    color: var(--text-grey);
    font-size: 18px; line-height: 1.55;
  }
  .back-brand {
    position: absolute;
    top: 126px; left: 300px;
    display: flex; align-items: flex-start; gap: 30px;
  }
  .back-brand .mark-square { width: 90px; height: 90px; background: var(--orange); margin-top: 20px; }
  .divider { width: 2px; height: 150px; background: var(--orange); }
  .back-title { text-align: center; padding-top: 16px; }
  .back-title .company-name { color: var(--orange); font-size: 38px; }
  .back-title .company-sub { color: var(--text-grey); font-size: 22px; }
  .back-title .company-phone { color: var(--orange); font-size: 22px; }
</style>
</head>
<body>

  <section class="card card-front" aria-label="Business card front">
    <svg class="panels" width="720" height="412" viewBox="0 0 720 412" aria-hidden="true">
      <defs>
        <linearGradient id="orangeSheen" x1="0" y1="0" x2="1" y2="0">
          <stop offset="0" stop-color="var(--orange)"/>
          <stop offset="0.55" stop-color="var(--orange-light)"/>
          <stop offset="1" stop-color="var(--orange)"/>
        </linearGradient>
      </defs>
      <polygon points="0,0 380,0 250,412 0,412" fill="url(#orangeSheen)"/>
      <polygon points="380,0 420,0 290,412 250,412" fill="var(--stripe)"/>
    </svg>

    <div class="company-block">
      <div class="company-name">HOLLOWAY PAVING</div>
      <div class="company-sub">SERVICE</div>
      <div class="company-phone">0418259730</div>
    </div>

    <div class="brand-feature">
      <span class="mark-square"></span>
      <span>HOLLOWAY PAVING</span>
    </div>

    <div class="contact-block">
      <div class="person-name">MARK HOLLOWAY</div>
      <div class="contact-line">0418259730</div>
      <div class="contact-line">markholloway@brightmail.com.au</div>
      <div class="contact-line">www.hollowaypaving.com.au</div>
    </div>

    <div class="abn">ABN 62318470915</div>
  </section>

  <section class="card card-back" aria-label="Business card back">
    <div class="services">
      Excavation | Exposed &amp; colour concrete<br>
      House &amp; shed slabs | Driveways | Landing &amp; steps
    </div>

    <div class="back-brand">
      <span class="mark-square"></span>
      <span class="divider"></span>
      <div class="back-title">
        <div class="company-name">HOLLOWAY PAVING</div>
        <div class="company-sub">SERVICE</div>
        <div class="company-phone">0418259730</div>
      </div>
    </div>
  </section>

</body>
</html>
```